TA BRAMLEY BUSINESS CARD DESIGN PROJECT

We need to utilize our logo that was expertly created on PixelHarbor and now need to match this with a business card design.

```html
<!DOCTYPE html>
<html lang="en">
<head>
<meta charset="utf-8">
<title>TA Bramley Business Card</title>
<link href="https://fonts.googleapis.com/css2?family=Montserrat:wght@400;600;700&display=swap" rel="stylesheet">
<style>
  :root {
    --brand-blue: #0f55a8;
    --ink: #2a2a2a;
    --card-white: #ffffff;
    --backdrop: #e9e4da;
  }
  * { box-sizing: border-box; margin: 0; padding: 0; }
  html, body {
    width: 1200px;
    height: 900px;
    overflow: hidden;
    background: var(--backdrop);
    font-family: "Montserrat", sans-serif;
  }
  .canvas { position: relative; width: 1200px; height: 900px; }
  .card {
    position: absolute;
    left: 310px;
    width: 582px;
    height: 332px;
    border-radius: 30px;
    overflow: hidden;
    box-shadow: 0 6px 18px rgba(0,0,0,0.18);
  }
  .card-front { top: 86px; background: var(--card-white); }
  .card-back  { top: 470px; background: var(--brand-blue); }

  .brand-name {
    font-weight: 700;
    color: var(--brand-blue);
    letter-spacing: 0.06em;
    line-height: 1;
  }
  .front-brand {
    position: absolute;
    left: 24px;
    top: 34px;
    display: flex;
    align-items: center;
    gap: 12px;
  }
  .front-brand .brand-mark {
    width: 30px; height: 30px; background: var(--brand-blue);
  }
  .front-brand .brand-name { font-size: 32px; }

  .holder {
    position: absolute;
    right: 22px;
    top: 20px;
    text-align: right;
  }
  .holder-name {
    font-size: 20px;
    font-weight: 700;
    color: var(--brand-blue);
    letter-spacing: 0.01em;
  }
  .holder-title {
    font-size: 15px;
    color: var(--ink);
    margin-top: 2px;
  }

  .address {
    position: absolute;
    left: 24px;
    top: 196px;
    font-size: 15px;
    line-height: 20px;
    color: var(--ink);
  }
  .contact-list {
    position: absolute;
    left: 24px;
    top: 252px;
    list-style: none;
    font-size: 15px;
    line-height: 20px;
    color: var(--ink);
  }
  .contact-list li { display: flex; align-items: center; gap: 5px; }
  .contact-list svg { width: 13px; height: 13px; fill: var(--brand-blue); flex: none; }

  .front-feature {
    position: absolute;
    left: 240px;
    top: 204px;
    width: 342px;
    height: 128px;
    display: flex;
    align-items: center;
    justify-content: flex-end;
    padding-right: 20px;
  }
  .front-feature .brand-name { font-size: 44px; }

  .back-brand {
    position: absolute;
    inset: 0;
    display: flex;
    flex-direction: column;
    align-items: center;
    justify-content: center;
    gap: 18px;
  }
  .back-brand .brand-mark { width: 54px; height: 54px; background: var(--card-white); }
  .back-brand .brand-name { color: var(--card-white); font-size: 58px; letter-spacing: 0.12em; }
</style>
</head>
<body>
<main class="canvas">

  <section class="card card-front">
    <div class="front-brand">
      <span class="brand-mark"></span>
      <span class="brand-name">TA BRAMLEY</span>
    </div>

    <div class="holder">
      <p class="holder-name">NORA ELLISON</p>
      <p class="holder-title">Managing Director</p>
    </div>

    <p class="address">Your address, City<br>State, Zip 1234</p>

    <ul class="contact-list">
      <li>
        <svg viewBox="0 0 16 16" aria-hidden="true"><path d="M1 6c0-2 3-3 7-3s7 1 7 3v1.5h-3.5V6h-7v1.5H1zM4 8h8l2 5H2z"/></svg>
        123 456 789
      </li>
      <li>
        <svg viewBox="0 0 16 16" aria-hidden="true"><path d="M1 4h14v1.2L8 9.5 1 5.2zM1 6.8l7 4.3 7-4.3V13H1z"/></svg>
        info@yourgmail.com
      </li>
      <li>
        <svg viewBox="0 0 16 16" aria-hidden="true"><circle cx="8" cy="8" r="7"/><path d="M4 5c2 0 2 2 4 2s1 3-1 3-1 3-2 3-2-4-2-5-1-3 1-3z" fill="#fff"/></svg>
        www.yourwebsite.com
      </li>
    </ul>

    <div class="front-feature">
      <span class="brand-name">TA BRAMLEY</span>
    </div>
  </section>

  <section class="card card-back">
    <div class="back-brand">
      <span class="brand-mark"></span>
      <span class="brand-name">TA BRAMLEY</span>
    </div>
  </section>

</main>
</body>
</html>
```